Wandering Rooms Stationary Set

Wandering Rooms is a bespoke interior design firm set to provide services to VIP clients with elegance and minimalism is the main theme for our stationary set. We require a full stationary set covering A4 letterhead, A4 & A3 envelopes, business cards, USB's, CDs, email signature and any other item the designer sees fit. logo is already designed and finalized, and we require the designer to use it as is without modifying the logo.

Address to be used on letterhead / business cards ...etc shall be as follows:

Phone : +971 2 518 2047
P.O. Box : 309186
Address: Block C&D, Bldg. 47, Court 12, Abu Dhabi, United Arab Emirates
Website: www.wanderingrooms-example.com

Target Market(s)

VIP Clients

Industry/Entity Type

Interior Design

Font styles to use
Other font styles liked:
• something to be unique

Colors

Designer to choose colors to be used in the design.

Requirements
Must have
• Elegant, minimalistic
Nice to have
• Simple yet elegant design having a sharp yet clean cut format
Should not have
• No additional colours, just colours that are used in the logo (silver, black or gold)

```html
<!DOCTYPE html>
<html lang="en">
<head>
<meta charset="utf-8">
<title>Wandering Rooms – Business Card</title>
<link href="https://fonts.googleapis.com/css2?family=EB+Garamond:wght@400&display=swap" rel="stylesheet">
<style>
  :root {
    --backdrop: #2b2521;
    --card: #1d1d1f;
    --silver: #cfd0d3;
    --silver-soft: #9a9b9e;
    --muted: #6c6c6f;
    --deep: #3c3c3f;
    --icon-fill: #5e5e61;
  }
  * { margin: 0; padding: 0; box-sizing: border-box; }
  html, body {
    width: 1200px; height: 715px; overflow: hidden;
    background: var(--backdrop);
    font-family: "EB Garamond", Georgia, serif;
  }
  .stage {
    position: relative; width: 1200px; height: 715px;
  }
  .card {
    position: absolute; top: 208px;
    width: 520px; height: 300px;
    background: var(--card);
    box-shadow: 0 14px 30px rgba(0,0,0,0.45);
  }
  .card--front { left: 50px; }
  .card--back { left: 630px; }

  .wordmark {
    position: absolute;
    color: var(--silver);
    font-weight: 400;
    font-size: 34px;
    letter-spacing: 1px;
    white-space: nowrap;
  }
  .card--front .wordmark { left: 0; right: 0; top: 112px; text-align: center; }
  .card--front .website {
    position: absolute; left: 0; right: 0; top: 196px;
    text-align: center; color: var(--silver);
    font-size: 12px; letter-spacing: 2px;
  }

  .card--back .wordmark { right: 38px; top: 118px; font-size: 30px; }
  .holder { position: absolute; left: 38px; top: 34px; }
  .holder__name { color: var(--deep); font-size: 17px; letter-spacing: 0.5px; }
  .holder__role { color: var(--deep); font-size: 11px; margin-top: 1px; }

  .contacts { position: absolute; left: 38px; top: 178px; list-style: none; }
  .contacts li {
    display: flex; align-items: center; gap: 10px;
    color: var(--muted); font-size: 11px; height: 19px;
  }
  .contacts svg { width: 13px; height: 13px; flex: none; }

  .address {
    position: absolute; right: 38px; bottom: 34px;
    text-align: right; color: var(--deep);
    font-size: 12px; line-height: 1.35;
  }
</style>
</head>
<body>
<main class="stage">
  <section class="card card--front">
    <div class="wordmark">Wandering Rooms</div>
    <div class="website">www.wanderingrooms-example.com</div>
  </section>

  <section class="card card--back">
    <div class="holder">
      <div class="holder__name">Mira Haddad</div>
      <div class="holder__role">Director</div>
    </div>

    <div class="wordmark">Wandering Rooms</div>

    <ul class="contacts">
      <li>
        <svg viewBox="0 0 14 14" aria-hidden="true"><circle cx="7" cy="7" r="7" fill="var(--icon-fill)"/><path d="M4.4 3.6l1.3-.3.8 1.8-.8.6c.4.9 1.1 1.6 2 2l.6-.8 1.8.8-.3 1.3c-3 .2-5.6-2.4-5.4-5.4z" fill="var(--card)"/></svg>
        +971 2 518 2047
      </li>
      <li>
        <svg viewBox="0 0 14 14" aria-hidden="true"><circle cx="7" cy="7" r="7" fill="var(--icon-fill)"/><rect x="3.5" y="4.5" width="7" height="5" fill="none" stroke="var(--card)" stroke-width="0.9"/><path d="M3.5 4.5L7 7.3l3.5-2.8" fill="none" stroke="var(--card)" stroke-width="0.9"/></svg>
        studio@wanderingrooms-example.com
      </li>
      <li>
        <svg viewBox="0 0 14 14" aria-hidden="true"><circle cx="7" cy="7" r="7" fill="var(--icon-fill)"/><rect x="3.8" y="5" width="6.4" height="4.6" fill="var(--card)"/><path d="M3.8 5L7 3.4 10.2 5" fill="none" stroke="var(--card)" stroke-width="0.9"/></svg>
        P.O. Box : 309186
      </li>
    </ul>

    <div class="address">
      Block C&amp;D, Bldg. 47<br>
      Court 12, Abu Dhabi, United Arab Emirates
    </div>
  </section>
</main>
</body>
</html>
```